Business Card Design

New business card design

Target Market(s)

Residential & Commercial Property Managers

Industry/Entity Type

Plumbing Services

Contact Information for Business Card

Name - Rowan Keddle, title - Director, Phone Number - 0431 286 517, email - rowan@tbk-plumbing.com.au, Company ABN - 73 215 904 386,

Font styles to use
Sans Serif

Colors
0054AA
0677BA
7BADD7
CADEEF
E8F1F8

```html
<!DOCTYPE html>
<html lang="en">
<head>
<meta charset="utf-8">
<title>TBK Plumbing – Business Card</title>
<link href="https://fonts.googleapis.com/css2?family=Montserrat:wght@400;500;700&display=swap" rel="stylesheet">
<style>
  :root {
    --stage: #cdd2d2;
    --paper: #efefed;
    --blue: #2ba8e0;
    --blue-deep: #0677ba;
    --ink: #15191c;
    --ink-soft: #3a3f43;
  }
  * { margin: 0; padding: 0; box-sizing: border-box; }
  html, body { width: 1200px; height: 881px; overflow: hidden; }
  body {
    background: var(--stage);
    font-family: "Montserrat", Arial, sans-serif;
    position: relative;
  }
  .card {
    position: absolute;
    top: 292px;
    width: 520px;
    height: 297px;
    background: var(--paper);
    border-bottom: 3px solid var(--blue);
    box-shadow: 0 14px 30px rgba(0,0,0,0.18);
    overflow: hidden;
  }
  .card--front { left: 50px; }
  .card--back { left: 630px; }

  /* front */
  .name-tab {
    position: absolute; left: 38px; top: 86px;
    width: 8px; height: 32px; background: var(--blue);
  }
  .person-name {
    position: absolute; left: 56px; top: 84px;
    font-size: 19px; font-weight: 700; color: var(--blue);
  }
  .person-title {
    position: absolute; left: 56px; top: 108px;
    font-size: 12px; font-weight: 400; color: var(--ink-soft);
  }
  .name-rule {
    position: absolute; left: 48px; top: 132px;
    width: 126px; height: 1px; background: var(--blue);
  }
  .contact {
    position: absolute; left: 48px;
    display: flex; align-items: center; gap: 7px;
    font-size: 12px; color: var(--ink-soft);
  }
  .contact--phone { top: 146px; }
  .contact--email { top: 166px; }
  .contact svg { width: 11px; height: 11px; fill: var(--blue); }
  .front-line { position: absolute; left: 0; top: 0; }
  .abn {
    position: absolute; left: 286px; top: 238px;
    font-size: 12px; color: var(--ink-soft);
  }
  .brand {
    position: absolute;
    display: flex; align-items: center; gap: 10px;
    font-weight: 500; color: var(--ink);
    white-space: nowrap;
  }
  .brand__dot { border-radius: 50%; background: var(--blue); flex: none; }
  .card--front .brand { left: 268px; top: 92px; font-size: 30px; }
  .card--front .brand__dot { width: 12px; height: 12px; }

  /* back */
  .card--back .brand {
    left: 50%; top: 50%; transform: translate(-50%, -50%);
    font-size: 48px;
  }
  .card--back .brand__dot { width: 18px; height: 18px; }
</style>
</head>
<body>

<section class="card card--front" aria-label="Business card front">
  <div class="name-tab"></div>
  <p class="person-name">Rowan Keddle</p>
  <p class="person-title">Director</p>
  <div class="name-rule"></div>

  <p class="contact contact--phone">
    <svg viewBox="0 0 24 24" aria-hidden="true"><path d="M6.6 10.8a15.1 15.1 0 0 0 6.6 6.6l2.2-2.2a1 1 0 0 1 1-.25 11.4 11.4 0 0 0 3.6.57 1 1 0 0 1 1 1V20a1 1 0 0 1-1 1A17 17 0 0 1 3 4a1 1 0 0 1 1-1h3.5a1 1 0 0 1 1 1c0 1.25.2 2.45.57 3.57a1 1 0 0 1-.25 1z"/></svg>
    0431 286 517
  </p>
  <p class="contact contact--email">
    <svg viewBox="0 0 24 24" aria-hidden="true"><path d="M2 5h20v14H2z M4 7v.5l8 5 8-5V7l-8 5z" fill-rule="evenodd"/></svg>
    rowan@tbk-plumbing.com.au
  </p>

  <svg class="front-line" width="520" height="297" viewBox="0 0 520 297" aria-hidden="true">
    <path d="M0 200 H222 C244 200 244 260 270 260 H440" fill="none" stroke="var(--blue)" stroke-width="1.2"/>
  </svg>
  <p class="abn">Company ABN - 73 215 904 386</p>

  <div class="brand"><span class="brand__dot"></span>TBK Plumbing</div>
</section>

<section class="card card--back" aria-label="Business card back">
  <div class="brand"><span class="brand__dot"></span>TBK Plumbing</div>
</section>

</body>
</html>
```